Vacation Rental Postcard Design

The Kingfisher's Perch is a vacation rental cottage. We want a postcard that can be used as promotional give-aways for visitors as well as something that can be given to the tourism board and local merchants to help us promote the rental.

Our tag line is" The Kingfisher's Perch - the finest perch on the ridge!". Should also include "Snohomish, WA USA"

We have also used "Come see what all of the buzz is about"

Want to include our info in small print on the mailing side portion of the postcard:

KLWT: www.klwtstays.example/417294
Chatterly: www.chatterly.example/thefinestperchontheridge

Target Market(s)

Couples, romantic, honeymooners, coming for wine tasting, hot air ballooning, hiking, enjoying nature

Industry/Entity Type

Tourism

```html
<!DOCTYPE html>
<html lang="en">
<head>
<meta charset="utf-8">
<title>The Kingfisher's Perch – Postcard Backs</title>
<link href="https://fonts.googleapis.com/css2?family=Bebas+Neue&family=Roboto+Condensed:wght@400;700&display=swap" rel="stylesheet">
<style>
  :root {
    --paper: #ffffff;
    --ink: #111111;
    --rule: #2a2a2a;
    --guide: #d6d6d6;
    --mark: #d9d9d9;
    --shadow: rgba(0,0,0,0.18);
    --sky-top: #e86a8a;
    --sky-low: #f2a05a;
    --room-wall: #c9a24a;
    --room-floor: #6b3b22;
    --bed-wall: #d8b24c;
    --bed-linen: #e9ebe2;
    --house-leaf: #5f8f3a;
    --house-siding: #2f6a4c;
    --house-ground: #8a6a4a;
  }
  * { box-sizing: border-box; margin: 0; padding: 0; }
  html, body { width: 1186px; height: 1200px; overflow: hidden; background: var(--paper); }
  .sheet { position: relative; width: 1186px; height: 1200px; }

  .sheet-title {
    position: absolute; left: 35px; top: 925px;
    transform: rotate(-90deg); transform-origin: 0 0;
    font-family: 'Bebas Neue', 'Arial Narrow', sans-serif;
    font-size: 150px; line-height: 110px; letter-spacing: 3px;
    color: var(--ink); white-space: nowrap; width: 650px; height: 110px;
  }

  .card {
    position: absolute; width: 468px; height: 360px;
    background: var(--paper);
    box-shadow: 2px 3px 6px var(--shadow);
    overflow: hidden;
  }
  .card--photos   { left: 183px; top: 37px; }
  .card--buzz     { left: 683px; top: 32px; }
  .card--house    { left: 189px; top: 419px; }
  .card--plain    { left: 692px; top: 419px; }
  .card--tagline  { left: 189px; top: 805px; }

  .guides { position: absolute; inset: 0; width: 100%; height: 100%; }
  .guides line { stroke: var(--guide); stroke-width: 1; stroke-dasharray: 4 4; }

  .stamp-box {
    position: absolute; right: 32px; top: 35px;
    width: 64px; height: 80px; border: 1px solid var(--ink);
  }
  .address-lines {
    position: absolute; right: 30px; bottom: 36px; width: 116px; height: 38px;
    border-top: 1px solid var(--rule); border-bottom: 1px solid var(--rule);
  }
  .address-lines::after {
    content: ""; position: absolute; left: 0; right: 0; top: 18px;
    border-top: 1px solid var(--rule);
  }

  .watermark {
    position: absolute; display: flex; align-items: center; gap: 10px;
    font-family: 'Bebas Neue', 'Arial Narrow', sans-serif;
    color: var(--mark); white-space: nowrap;
  }
  .watermark__dot { width: 34px; height: 34px; border-radius: 50%; background: var(--mark); flex: none; }
  .watermark__name { font-size: 26px; line-height: 1; }
  .watermark--large .watermark__dot { width: 46px; height: 46px; }
  .watermark--large .watermark__name { font-size: 36px; }

  .photo { position: absolute; }
  .photo--sunset  { left: 18px; top: 14px; width: 144px; height: 106px; background: linear-gradient(180deg, var(--sky-top), var(--sky-low) 60%, #2a1f25 85%); }
  .photo--living  { left: 18px; top: 127px; width: 144px; height: 107px; background: linear-gradient(180deg, var(--room-wall), #8a6a3a 60%, var(--room-floor)); }
  .photo--bedroom { left: 18px; top: 238px; width: 144px; height: 107px; background: linear-gradient(180deg, var(--bed-wall), #b89a50 50%, var(--bed-linen)); }
  .photo--house   { left: 0; top: 0; width: 193px; height: 100%; background: linear-gradient(180deg, var(--house-leaf) 0%, var(--house-siding) 45%, #3e5a48 65%, var(--house-ground) 100%); }

  .card-heading {
    position: absolute; left: 29px; top: 40px;
    font-family: 'Bebas Neue', 'Arial Narrow', sans-serif;
    font-size: 22px; line-height: 20px; color: var(--ink); letter-spacing: 0.3px;
  }
  .card-heading--small { font-size: 15px; line-height: 15px; }
  .message-lines {
    position: absolute; left: 29px; width: 213px;
    background: repeating-linear-gradient(180deg, var(--rule) 0 1px, transparent 1px 15.6px);
  }
  .message-lines--buzz { top: 143px; height: 190px; }
  .message-lines--tagline { top: 120px; height: 190px; }
  .signature-line { position: absolute; left: 29px; width: 113px; border-top: 1px solid var(--rule); }
  .card--buzz .signature-line { top: 118px; }
  .card--tagline .signature-line { top: 104px; }

  .contact-strip {
    position: absolute; left: 283px; top: 330px;
    transform: rotate(-90deg); transform-origin: 0 0;
    font-family: 'Roboto Condensed', 'Arial Narrow', sans-serif;
    font-size: 8px; line-height: 10px; color: var(--ink); white-space: nowrap;
  }
  .contact-strip__sep { margin: 0 8px; }

  .brand-mark {
    position: absolute; left: 312px; top: 152px; display: flex; align-items: center; gap: 5px;
    font-family: 'Bebas Neue', 'Arial Narrow', sans-serif; font-size: 13px; color: var(--ink); white-space: nowrap;
  }
  .brand-mark__dot { width: 13px; height: 13px; border-radius: 50%; background: var(--ink); flex: none; }
</style>
</head>
<body>
<main class="sheet">
  <h1 class="sheet-title">Choose Back</h1>

  <section class="card card--photos">
    <svg class="guides" viewBox="0 0 468 360" preserveAspectRatio="none"><line x1="0" y1="0" x2="468" y2="360"/><line x1="468" y1="0" x2="0" y2="360"/></svg>
    <div class="watermark" style="left:172px; top:150px;"><span class="watermark__dot"></span><span class="watermark__name">The Kingfisher's Perch</span></div>
    <div class="photo photo--sunset" role="img" aria-label="Pink and orange sunset behind silhouetted evergreen trees"></div>
    <div class="photo photo--living" role="img" aria-label="Cottage living and dining room with wood floors and flowers"></div>
    <div class="photo photo--bedroom" role="img" aria-label="Cottage bedroom with a white patterned bedspread"></div>
    <div class="stamp-box"></div>
    <div class="address-lines"></div>
  </section>

  <section class="card card--buzz">
    <svg class="guides" viewBox="0 0 468 360" preserveAspectRatio="none"><line x1="0" y1="0" x2="468" y2="360"/><line x1="468" y1="0" x2="0" y2="360"/></svg>
    <div class="watermark" style="left:165px; top:145px;"><span class="watermark__dot"></span><span class="watermark__name">The Kingfisher's Perch</span></div>
    <h2 class="card-heading">Come see what all<br>of the buzz is about</h2>
    <div class="signature-line"></div>
    <div class="message-lines message-lines--buzz"></div>
    <div class="stamp-box"></div>
    <div class="address-lines"></div>
  </section>

  <section class="card card--house">
    <svg class="guides" viewBox="0 0 468 360" preserveAspectRatio="none"><line x1="0" y1="0" x2="468" y2="360"/><line x1="468" y1="0" x2="0" y2="360"/></svg>
    <div class="photo photo--house" role="img" aria-label="Green cottage with red trim, garden shrubs and stone steps under leafy trees"></div>
    <div class="stamp-box"></div>
    <div class="address-lines"></div>
  </section>

  <section class="card card--plain">
    <svg class="guides" viewBox="0 0 468 360" preserveAspectRatio="none"><line x1="0" y1="0" x2="468" y2="360"/><line x1="468" y1="0" x2="0" y2="360"/></svg>
    <div class="watermark watermark--large" style="left:30px; top:120px;"><span class="watermark__dot"></span><span class="watermark__name">The Kingfisher's Perch</span></div>
    <div class="stamp-box"></div>
    <div class="address-lines"></div>
  </section>

  <section class="card card--tagline">
    <svg class="guides" viewBox="0 0 468 360" preserveAspectRatio="none"><line x1="0" y1="0" x2="468" y2="360"/><line x1="468" y1="0" x2="0" y2="360"/></svg>
    <h2 class="card-heading card-heading--small">The Kingfisher's Perch<br>– the finest perch on the ridge!</h2>
    <div class="signature-line"></div>
    <div class="message-lines message-lines--tagline"></div>
    <p class="contact-strip">www.klwtstays.example/417294<span class="contact-strip__sep">•</span>www.chatterly.example/thefinestperchontheridge</p>
    <div class="brand-mark"><span class="brand-mark__dot"></span><span>The Kingfisher's Perch</span></div>
    <div class="stamp-box"></div>
    <div class="address-lines"></div>
  </section>
</main>
</body>
</html>
```